Etiketten-Design für Rotwein
Zielgruppe
Weinkellerei aus Baden (Deutschland) mit Fokus im Lebensmittelhandel in Deutschland
Aufgabenstellung
Wir suchen ein Frontetikett für einen modernen badischen Rotwein (Cuvée Lumen) mit dem Namen 'Die stille Seite vom Hang'
Aus dem Etikett soll hervorgehen, dass es sich nicht um einen klassischen, leichten deutschen Rotwein handelt, sondern um einen kräftigen, gehaltvollen, mediterran anmutenden Rotwein mit purpurroter Farbe und vollmundigem, nachhaltigem Geschmack. (Geschmacksrichtung feinherb)
Zielgruppe Discount-Kunden, Männlich/Weiblich, Alter: 25-60 Jahre, wird für unter € 5,-/Fl. verkauft.
Weinbeschreibung:
Farbe: Ein wunderschönes tiefdunkles purpurrot mit violetten Reflexen
Duft: In der Nase zeigen sich Aromen nach Waldbeeren, sowie Anklänge von Rauch, Röstaromen, Nelke, etwas Vanille und dunkle Schokolade
Geschmack: Geschmacklich füllig und kraftvoll, Brombeeraromen und schön eingebundenen Tanninen. Langanhaltend intensiv im Abgang.
Anforderungen Etikett:
Maße: Höhe max. 120mm/Breite max. 80mm (darf auch kleiner oder quadratisch sein)
SK Etikett, Naturstruktur bis 90g (m²) (Ein - oder zweiteilig)
Eine figürliche Etikettenkontur ist möglich, es wird aber am rechten Etikettenrand eine gerade Spendekante benötigt um das Etikett maschinell verarbeiten zu können.
Als Flasche wird eine 0,75 L Bordeauxflasche (Farbe: grün) eingesetzt.
Verschluss: Longcap
Mögliche Veredelungen: Quelllack, Prägungen, Heissfolie, Glanzlack
Pflichtangaben:
Die stille Seite vom Hang

```html
<!DOCTYPE html>
<html lang="de">
<head>
<meta charset="utf-8">
<title>Die stille Seite vom Hang – Frontetikett</title>
<link rel="stylesheet" href="https://fonts.googleapis.com/css2?family=Raleway:wght@300;400&display=swap">
<style>
  :root {
    --backdrop: #141414;
    --label-black: #0b0b0b;
    --grape-light: #5a5a5a;
    --grape-mid: #2c2c2c;
    --title-white: #e6e6e6;
    --detail-grey: #8c8c8c;
  }
  html, body {
    margin: 0;
    padding: 0;
    width: 1000px;
    height: 1200px;
    overflow: hidden;
    background: var(--backdrop);
  }
  .canvas {
    position: relative;
    width: 1000px;
    height: 1200px;
  }
  .wine-label {
    position: absolute;
    left: 235px;
    top: 100px;
    width: 530px;
    height: 1000px;
    background: var(--label-black);
    overflow: hidden;
    font-family: "Raleway", sans-serif;
  }
  .grape-visual {
    position: absolute;
    left: 0;
    top: 0;
    width: 100%;
    height: 510px;
    background:
      radial-gradient(ellipse 55% 50% at 48% 40%, var(--grape-light) 0%, var(--grape-mid) 45%, transparent 80%),
      linear-gradient(180deg, var(--grape-mid) 0%, #1a1a1a 60%, var(--label-black) 100%);
  }
  .wine-title {
    position: absolute;
    left: 0;
    right: 0;
    top: 530px;
    margin: 0;
    text-align: center;
    color: var(--title-white);
    font-weight: 400;
    font-size: 22px;
    line-height: 44px;
    letter-spacing: 0.55em;
    text-transform: uppercase;
    padding-left: 0.55em;
  }
  .wine-details {
    position: absolute;
    left: 0;
    right: 0;
    top: 858px;
    margin: 0;
    text-align: center;
    color: var(--detail-grey);
    font-weight: 300;
    font-size: 17px;
    line-height: 27px;
    letter-spacing: 0.1em;
    text-transform: uppercase;
  }
  .divider { padding: 0 0.5em; }
</style>
</head>
<body>
  <main class="canvas">
    <section class="wine-label">
      <div class="grape-visual" role="img" aria-label="Schwarz-weiße Nahaufnahme einer dunklen Traubenrebe mit Wassertropfen, die nach unten ins Schwarz übergeht"></div>
      <h1 class="wine-title">Die stille Seite<br>vom Hang</h1>
      <p class="wine-details">
        Cuvée Lumen<span class="divider">|</span>Kraftvoll<br>
        Langanhaltend<span class="divider">|</span>Intensiv
      </p>
    </section>
  </main>
</body>
</html>
```